Heritage Hollow Business Cards

Require a business card design. <br/><br/>Needs to include logo (either round or long version) plus these details:<br/>Maya Torvell<br/>Heritage Hollow<br/>maya@kelvadtrading.com.au<br/>02 6481 7395<br/>PO Box Glenwarra NSW 2791<br/>www.heritagehollow.com.au<br/><br/>I need in an editable format so that I can create for multiple staff members. <br/><br/>

Target Market(s)

We are an online store selling renovation products to home owners are builders. Looking for a classic classy design.

Industry/Entity Type

Home And Garden

Contact Information for Business Card

Maya Torvell
Heritage Hollow
maya@kelvadtrading.com.au
02 6481 7395
PO Box Glenwarra NSW 2791
www.heritagehollow.com.au

Colors

Designer to choose colors to be used in the design.

Requirements
Must have
• Must include Logo.

```html
<!DOCTYPE html>
<html lang="en">
<head>
<meta charset="utf-8">
<title>Heritage Hollow Business Cards</title>
<link rel="stylesheet" href="https://fonts.googleapis.com/css2?family=Work+Sans:wght@400;500;700&display=swap">
<style>
  :root {
    --backdrop: #e4e4e4;
    --card: #ffffff;
    --ink: #1c1c1c;
    --muted: #5a5a5a;
    --rule: #6b6b6b;
  }
  * { margin: 0; padding: 0; box-sizing: border-box; }
  html, body { width: 1200px; height: 1001px; overflow: hidden; }
  body {
    background: var(--backdrop);
    font-family: "Work Sans", Arial, sans-serif;
    color: var(--ink);
    position: relative;
  }
  .card {
    position: absolute;
    left: 306px;
    width: 587px;
    height: 336px;
    background: var(--card);
  }
  .card--front { top: 135px; }
  .card--back { top: 523px; }

  .brand-mark {
    position: absolute;
    border: 1px solid var(--rule);
    border-radius: 50%;
    display: flex;
    align-items: center;
    justify-content: center;
    text-align: center;
    font-weight: 500;
    color: var(--ink);
    line-height: 1.1;
  }
  .card--front .brand-mark {
    left: 382px; top: 33px; width: 160px; height: 160px;
    font-size: 21px; padding-top: 40px;
  }
  .card--back .brand-mark {
    left: 193px; top: 42px; width: 216px; height: 216px;
    font-size: 29px; padding-top: 54px;
  }

  .holder-name {
    position: absolute; left: 37px; top: 183px;
    font-size: 25px; font-weight: 700; letter-spacing: 0.8px;
  }
  .holder-role {
    position: absolute; left: 37px; top: 215px;
    font-size: 14px; color: var(--muted); letter-spacing: 0.4px;
  }
  .role-rule {
    position: absolute; left: 107px; top: 225px;
    width: 446px; height: 1px; background: var(--rule);
  }
  .contact-list {
    position: absolute; left: 35px; top: 246px;
    list-style: none;
  }
  .contact-list li {
    display: flex; align-items: center; gap: 7px;
    height: 20px; font-size: 14.5px; color: var(--muted);
  }
  .contact-list svg { width: 13px; height: 13px; flex: none; }
  .contact-list strong { font-weight: 500; color: var(--ink); }
  .postal-address {
    position: absolute; left: 416px; top: 265px;
    font-style: normal; font-size: 14.5px; line-height: 20px;
    color: var(--muted); letter-spacing: 0.3px;
  }

  .web-footer {
    position: absolute; left: 32px; right: 32px; top: 288px;
    display: flex; align-items: center; gap: 8px;
    font-size: 14.5px; letter-spacing: 2.2px; color: var(--ink);
  }
  .web-footer::before, .web-footer::after {
    content: ""; flex: 1; height: 1px; background: var(--rule);
  }
  .web-footer strong { font-weight: 500; }
</style>
</head>
<body>
  <section class="card card--front" aria-label="Business card front">
    <div class="brand-mark">Heritage<br>Hollow</div>
    <h1 class="holder-name">Maya Torvell</h1>
    <p class="holder-role">Director</p>
    <div class="role-rule"></div>
    <ul class="contact-list">
      <li>
        <svg viewBox="0 0 13 13" aria-hidden="true"><rect width="13" height="13" rx="3" fill="#1c1c1c"/><path d="M4 3.2c.4-.3.9-.2 1.1.2l.6 1.2c.2.4 0 .7-.3 1l-.3.3c.4.9 1.1 1.6 2 2l.3-.3c.3-.3.6-.5 1-.3l1.2.6c.4.2.5.7.2 1.1-.5.7-1.3 1-2.1.7A6.3 6.3 0 0 1 3.4 5.3C3.1 4.5 3.4 3.7 4 3.2z" fill="#fff"/></svg>
        02 6481 7395
      </li>
      <li>
        <svg viewBox="0 0 13 13" aria-hidden="true"><rect width="13" height="13" rx="3" fill="#1c1c1c"/><rect x="2.8" y="3.8" width="7.4" height="5.4" rx=".6" fill="none" stroke="#fff" stroke-width="1"/><path d="M3 4.2l3.5 2.6L10 4.2" fill="none" stroke="#fff" stroke-width="1"/></svg>
        maya@kelvadtrading.com.au
      </li>
      <li>
        <svg viewBox="0 0 13 13" aria-hidden="true"><rect width="13" height="13" rx="3" fill="#1c1c1c"/><circle cx="6.5" cy="6.5" r="3.6" fill="none" stroke="#fff" stroke-width=".9"/><ellipse cx="6.5" cy="6.5" rx="1.5" ry="3.6" fill="none" stroke="#fff" stroke-width=".8"/><path d="M2.9 6.5h7.2" stroke="#fff" stroke-width=".8"/></svg>
        <span>www.<strong>heritagehollow</strong>.com.au</span>
      </li>
    </ul>
    <address class="postal-address">PO Box<br>Glenwarra NSW 2791</address>
  </section>

  <section class="card card--back" aria-label="Business card back">
    <div class="brand-mark">Heritage<br>Hollow</div>
    <p class="web-footer"><span>www.<strong>heritagehollow</strong>.com.au</span></p>
  </section>
</body>
</html>
```